Vorlanta PowerPoint Template

I have a company called Vorlanta, LLC and my company logo is already designed. I need a PowerPoint template that I will be using to pitch potential investors and business partners. This should be a very professional-looking template that leverages the company logo colors and really pops. The company is an AI product research and development company.

```html
<!DOCTYPE html>
<html lang="en">
<head>
<meta charset="utf-8">
<title>Vorlanta – Presentation Template</title>
<link href="https://fonts.googleapis.com/css2?family=Poppins:wght@400;500;600;700;800&display=swap" rel="stylesheet">
<style>
:root{
  --canvas:#d5d7da;
  --ink:#050303;
  --red:#c8161d;
  --red-deep:#7a0c10;
  --orange:#ee7a22;
  --yellow:#f6a81f;
  --white:#ffffff;
  --muted:#d9d9d9;
  --panel:#2a0a0b;
}
*{margin:0;padding:0;box-sizing:border-box}
html,body{width:1200px;height:2440px;overflow:hidden;background:var(--canvas)}
body{position:relative;font-family:"Poppins",sans-serif;color:var(--white)}
.slide{position:absolute;width:481px;height:271px;background:var(--ink);overflow:hidden}
.slide.glow::before{content:"";position:absolute;inset:0;
  background:
   radial-gradient(ellipse 22% 14% at 6% 100%,rgba(246,168,31,.85),transparent 70%),
   radial-gradient(ellipse 35% 16% at 42% 100%,rgba(200,22,29,.75),transparent 75%),
   radial-gradient(ellipse 30% 15% at 85% 100%,rgba(200,22,29,.6),transparent 75%);}
.abs{position:absolute}
.c1{left:106px}.c2{left:610px}
.brand{position:absolute;top:16px;right:20px;display:flex;align-items:center;gap:3px;font-weight:700;font-size:10px;color:var(--white)}
.brand .dot{width:9px;height:9px;border-radius:50%;background:var(--red)}
.side{position:absolute;left:457px;top:190px;width:9px;height:62px;border:.6px solid #777;border-radius:5px;writing-mode:vertical-rl;font-size:3.5px;color:#aaa;display:flex;align-items:center;justify-content:center}
.pg{position:absolute;left:458px;top:258px;font-size:4px;color:#aaa}
.tag{position:absolute;font-size:4px;padding:1px 5px;border:.7px solid var(--red);border-radius:4px;color:var(--white)}
.title{position:absolute;font-weight:600;font-size:18px;line-height:1.15}
.body{position:absolute;font-size:6px;line-height:1.3;color:var(--muted)}
.label{font-size:6px;color:var(--red)}
.num{position:absolute;font-weight:700;color:var(--yellow)}
.ico{position:absolute;width:20px;height:20px;border-radius:50%;background:var(--red);display:flex;align-items:center;justify-content:center}
.ico.y{background:var(--yellow)}
.ico svg{width:11px;height:11px;stroke:#fff;fill:none;stroke-width:1.4;stroke-linecap:round}
.photo{position:absolute;border-radius:50%}
.agenda-item{position:absolute;left:248px;display:flex;align-items:center;gap:9px;font-size:10px;font-weight:600}
.agenda-item b{width:25px;height:23px;background:var(--yellow);color:#111;display:flex;align-items:center;justify-content:center;font-size:14px;font-weight:700}
.funnel-bar{position:absolute;border-radius:10px;font-size:6px;display:flex;align-items:center;justify-content:center;text-align:center;color:#fff}
</style>
</head>
<body>

<!-- Cover -->
<section class="slide glow c1" style="top:44px">
  <div class="abs" style="left:36px;top:44px;display:flex;align-items:center;gap:8px;font-weight:700;font-size:34px">
    <span style="width:40px;height:40px;border-radius:50%;background:var(--red)"></span>Vorlanta</div>
  <div class="abs" style="left:49px;top:118px;font-weight:600;font-size:18px;line-height:1.25">Our Product for<br>the better<br><span style="color:var(--red);font-size:24px;font-weight:700">Future.</span></div>
  <div class="abs" style="left:48px;top:212px;width:128px;height:22px;border:1px solid var(--red);border-radius:11px;font-size:8px;letter-spacing:1px;display:flex;align-items:center;justify-content:center">www.vorlanta.com</div>
  <div class="abs" role="img" aria-label="Chrome humanoid robot in thinking pose" style="left:275px;top:20px;width:190px;height:251px;border-radius:90px 90px 0 0;background:radial-gradient(ellipse at 50% 40%,#9aa3ad,#3c4148 60%,transparent 80%)"></div>
</section>

<!-- Agenda -->
<section class="slide c2" style="top:44px">
  <div class="photo" role="img" aria-label="Robotic hand touching a glowing sphere" style="left:-110px;top:-70px;width:320px;height:320px;background:radial-gradient(circle at 45% 45%,#b24a4f,#5a1014 60%,#2b0506);border:10px solid var(--red)"></div>
  <div class="brand"><span class="dot"></span>Vorlanta</div>
  <span class="tag" style="left:248px;top:35px">Business</span>
  <div class="title" style="left:248px;top:46px">Agenda</div>
  <div class="agenda-item" style="top:88px"><b>01</b>Lorem ipsum dolor</div>
  <div class="agenda-item" style="top:122px"><b>02</b>Lorem ipsum dolor</div>
  <div class="agenda-item" style="top:156px"><b>03</b>Lorem ipsum dolor</div>
  <div class="agenda-item" style="top:190px"><b>04</b>Lorem ipsum dolor</div>
  <div class="agenda-item" style="top:224px"><b>05</b>Lorem ipsum dolor</div>
  <div class="side">www.vorlanta.com</div><div class="pg">02</div>
</section>

<!-- Welcome -->
<section class="slide glow c1" style="top:339px">
  <div class="brand"><span class="dot"></span>Vorlanta</div>
  <span class="tag" style="left:35px;top:30px">Message</span>
  <div class="title" style="left:35px;top:40px">Welcome</div>
  <p class="body" style="left:33px;top:78px;width:150px">Lorem ipsum dolor sit amet, consectetuer adipiscing elit, sed diam nonummy nibh euismod tincidunt ut laoreet dolore magna aliquam erat volutpat. Ut wisi enim ad minim veniam, quis nostrud exerci tation ullamcorper suscipit lobortis nisl ut aliquip ex ea commodo consequat. Duis autem vel eum iriure dolor in hendrerit in vulputate</p>
  <div class="abs" style="left:199px;top:58px;width:100px;height:150px;border:2px solid var(--orange);border-right:none;border-bottom:none"></div>
  <div class="abs" role="img" aria-label="Digital human head made of glowing particles" style="left:205px;top:63px;width:105px;height:150px;background:radial-gradient(ellipse at 45% 40%,#c65a1b,#3a1206 60%,#0d0503)"></div>
  <div class="abs" style="left:33px;top:181px;width:200px;height:30px;background:var(--red);font-size:6px;line-height:1.3;padding:6px 10px">Lorem ipsum dolor sit amet, consectetuer adipiscing elit, sed diam nonummy nibh euismod</div>
  <div class="num" style="left:322px;top:58px;font-size:24px">84%</div>
  <div class="body" style="left:323px;top:90px;width:105px"><span class="label">Lorem ipsum dolor</span><br>Ut wisi enim ad minim veniam, quis nostrud exerci tation ullamcorper</div>
  <div class="num" style="left:322px;top:138px;font-size:24px">260%</div>
  <div class="body" style="left:323px;top:170px;width:105px"><span class="label">Lorem ipsum dolor</span><br>Ut wisi enim ad minim veniam, quis nostrud exerci tation ullamcorper</div>
  <div class="side">www.vorlanta.com</div><div class="pg">02</div>
</section>

<!-- AI intro with circle -->
<section class="slide glow c2" style="top:339px">
  <div class="photo" role="img" aria-label="Person wearing a VR headset in red light" style="left:268px;top:-10px;width:225px;height:225px;background:radial-gradient(circle at 50% 45%,#b4686c,#5c2a3a 60%,#2a1220);border:5px solid var(--red)"></div>
  <div class="brand"><span class="dot"></span>Vorlanta</div>
  <span class="tag" style="left:35px;top:30px">Product</span>
  <div class="title" style="left:35px;top:42px">Artificial Inteligence<br>for the greater future.</div>
  <p class="body" style="left:35px;top:100px;width:190px">Lorem ipsum dolor sit amet, consectetuer adipiscing elit, sed diam nonummy nibh euismod tincidunt ut laoreet dolore magna aliquam erat volutpat. Ut wisi enim ad minim veniam, quis nostrud exerci tation ullamcorper suscipit lobortis nisl ut aliquip ex ea commodo consequat. Duis autem vel eum iriure dolor in hendrerit in vulputate</p>
  <div class="ico" style="left:35px;top:178px;width:26px;height:26px"><svg viewBox="0 0 12 12"><path d="M3 9l6-6M5 3h4v4"/></svg></div>
  <p class="body" style="left:70px;top:180px;width:110px">Ut wisi enim ad minim veniam, quis nostrud exerci tation ullamcorper</p>
  <div class="side">www.vorlanta.com</div><div class="pg">02</div>
</section>

<!-- Stats wedge -->
<section class="slide glow c1" style="top:633px">
  <div class="abs" style="left:-120px;top:-20px;width:300px;height:310px;border-radius:50%;background:linear-gradient(160deg,var(--red),var(--red-deep))"></div>
  <div class="abs" role="img" aria-label="Purple network sphere" style="left:-60px;top:30px;width:140px;height:200px;border-radius:50%;background:radial-gradient(circle at 40% 50%,#a34fd0,#4a1a7a 60%,transparent 75%)"></div>
  <div class="abs" style="left:68px;top:24px;width:66px;height:66px;border-radius:50%;background:#070303"></div>
  <div class="abs" style="left:95px;top:105px;width:66px;height:66px;border-radius:50%;background:#070303"></div>
  <div class="abs" style="left:68px;top:183px;width:66px;height:66px;border-radius:50%;background:#070303"></div>
  <div class="num" style="left:80px;top:38px;font-size:17px">84%</div><div class="body" style="left:80px;top:60px;width:40px;color:#fff">Lorem ipsum dolor sit</div>
  <div class="num" style="left:107px;top:119px;font-size:17px">84%</div><div class="body" style="left:107px;top:141px;width:40px;color:#fff">Lorem ipsum dolor sit</div>
  <div class="num" style="left:74px;top:197px;font-size:17px">84%</div><div class="body" style="left:74px;top:219px;width:40px;color:#fff">Lorem ipsum dolor sit</div>
  <div class="brand"><span class="dot"></span>Vorlanta</div>
  <span class="tag" style="left:206px;top:46px">Product</span>
  <div class="title" style="left:206px;top:58px">Artificial Inteligence<br>for the greater future.</div>
  <p class="body" style="left:206px;top:118px;width:220px">Lorem ipsum dolor sit amet, consectetuer adipiscing elit, sed diam nonummy nibh euismod tincidunt ut laoreet dolore magna aliquam erat volutpat. Ut wisi enim ad minim veniam, quis nostrud exerci tation ullamcorper suscipit lobortis nisl ut aliquip ex ea commodo consequat. Duis autem vel eum iriure dolor in hendrerit in vulputate</p>
  <div class="ico" style="left:206px;top:190px;width:26px;height:26px"><svg viewBox="0 0 12 12"><path d="M3 9l6-6M5 3h4v4"/></svg></div>
  <p class="body" style="left:240px;top:192px;width:70px">Ut wisi enim ad minim veniam, quis nostrud exerci tation ullamcorper</p>
  <div class="ico y" style="left:323px;top:190px;width:26px;height:26px"><svg viewBox="0 0 12 12"><circle cx="6" cy="5" r="3"/><path d="M5 10h2"/></svg></div>
  <p class="body" style="left:357px;top:192px;width:70px">Ut wisi enim ad minim veniam, quis nostrud exerci tation ullamcorper</p>
  <div class="side">www.vorlanta.com</div><div class="pg">02</div>
</section>

<!-- Heading with three circles -->
<section class="slide glow c2" style="top:633px">
  <div class="brand"><span class="dot"></span>Vorlanta</div>
  <span class="tag" style="left:44px;top:40px">Business</span>
  <div class="title" style="left:44px;top:50px">Heading</div>
  <svg class="abs" style="left:45px;top:115px" width="380" height="20"><path d="M0 18l25-12h60M230 4h170" stroke="#8a1a1a" stroke-width=".8" fill="none"/></svg>
  <div class="photo" role="img" aria-label="Cyber face in blue and red" style="left:203px;top:37px;width:74px;height:74px;background:radial-gradient(circle,#c53a55,#274b8a 70%)"></div>
  <div class="photo" role="img" aria-label="Robot working at a desk" style="left:124px;top:96px;width:88px;height:88px;background:radial-gradient(circle,#c98a55,#5a2c1a 75%)"></div>
  <div class="photo" role="img" aria-label="Robot face close-up" style="left:225px;top:120px;width:64px;height:64px;background:radial-gradient(circle,#b9583a,#3a3230 75%)"></div>
  <div class="num" style="left:292px;top:38px;font-size:26px">02</div>
  <div class="body" style="left:293px;top:70px;width:110px"><span class="label">Lorem ipsum dolor</span><br>Ut wisi enim ad minim veniam, quis nostrud exerci tation ullamcorper</div>
  <div class="num" style="left:46px;top:145px;font-size:26px">01</div>
  <div class="body" style="left:46px;top:177px;width:110px"><span class="label">Lorem ipsum dolor</span><br>Ut wisi enim ad minim veniam, quis nostrud exerci tation ullamcorper</div>
  <div class="num" style="left:311px;top:145px;font-size:26px">03</div>
  <div class="body" style="left:311px;top:177px;width:110px"><span class="label">Lorem ipsum dolor</span><br>Ut wisi enim ad minim veniam, quis nostrud exerci tation ullamcorper</div>
  <div class="side">www.vorlanta.com</div><div class="pg">02</div>
</section>

<!-- Product banner -->
<section class="slide glow c1" style="top:929px">
  <div class="abs" style="left:0;top:0;width:481px;height:130px;background:linear-gradient(100deg,var(--red),var(--orange) 60%,var(--yellow))"></div>
  <div class="abs" style="left:0;top:118px;width:520px;height:200px;border-radius:70px 0 0 0;background:var(--ink)"></div>
  <div class="abs" style="left:400px;top:0;width:120px;height:140px;border-radius:0 0 0 90px;background:linear-gradient(100deg,var(--orange),var(--yellow))"></div>
  <div class="abs" role="img" aria-label="White robot holding a magnifying glass" style="left:300px;top:30px;width:140px;height:225px;border-radius:60px;background:radial-gradient(ellipse,#d8d8d8,#6d6d6d 60%,transparent 78%)"></div>
  <div class="brand"><span class="dot"></span>Vorlanta</div>
  <span class="tag" style="left:45px;top:38px;border-color:#fff">Business</span>
  <div class="title" style="left:45px;top:48px">Our Product for<br>the better Future.</div>
  <div class="abs" style="left:60px;top:150px;font-size:12px">➹</div>
  <div class="body" style="left:55px;top:173px;width:60px"><span class="label">Lorem ipsum</span><br>Ut wisi enim ad minim veniam, quis nostrud exerci tation ullamcorper</div>
  <div class="abs" style="left:140px;top:150px;font-size:12px">♡</div>
  <div class="body" style="left:136px;top:173px;width:60px"><span class="label">Lorem ipsum</span><br>Ut wisi enim ad minim veniam, quis nostrud exerci tation ullamcorper</div>
  <div class="abs" style="left:226px;top:150px;font-size:12px">✎</div>
  <div class="body" style="left:222px;top:173px;width:60px"><span class="label">Lorem ipsum</span><br>Ut wisi enim ad minim veniam, quis nostrud exerci tation ullamcorper</div>
  <div class="side">www.vorlanta.com</div><div class="pg">02</div>
</section>

<!-- AI with orange panel -->
<section class="slide glow c2" style="top:929px">
  <div class="photo" role="img" aria-label="Human hand reaching toward a glowing AI brain" style="left:30px;top:32px;width:146px;height:146px;background:radial-gradient(circle at 55% 45%,#c24063,#2b4a9a 65%,#0a1630)"></div>
  <div class="abs" style="left:0;top:136px;width:180px;height:140px;border-radius:0 36px 0 0;background:linear-gradient(90deg,var(--red),var(--yellow))"></div>
  <p class="body" style="left:36px;top:160px;width:125px;color:#fff">Lorem ipsum dolor sit amet, consectetuer adipiscing elit, sed diam nonummy nibh euismod tincidunt ut laoreet dolore magna aliquam erat volutpat. Ut wisi enim ad minim veniam, quis nostrud exerci tation ullamcorper suscipit lobortis nisl ut aliquip ex ea commodo consequat. Duis autem vel eum iriure dolor in hendrerit in vulputate</p>
  <div class="brand"><span class="dot"></span>Vorlanta</div>
  <span class="tag" style="left:206px;top:46px">Product</span>
  <div class="title" style="left:206px;top:58px">Artificial Inteligence<br>for the greater future.</div>
  <p class="body" style="left:206px;top:118px;width:220px">Lorem ipsum dolor sit amet, consectetuer adipiscing elit, sed diam nonummy nibh euismod tincidunt ut laoreet dolore magna aliquam erat volutpat. Ut wisi enim ad minim veniam, quis nostrud exerci tation ullamcorper suscipit lobortis nisl ut aliquip ex ea commodo consequat. Duis autem vel eum iriure dolor in hendrerit in vulputate</p>
  <div class="ico" style="left:206px;top:192px;width:26px;height:26px"><svg viewBox="0 0 12 12"><path d="M3 9l6-6M5 3h4v4"/></svg></div>
  <p class="body" style="left:240px;top:194px;width:70px">Ut wisi enim ad minim veniam, quis nostrud exerci tation ullamcorper</p>
  <div class="ico y" style="left:323px;top:192px;width:26px;height:26px"><svg viewBox="0 0 12 12"><circle cx="6" cy="5" r="3"/><path d="M5 10h2"/></svg></div>
  <p class="body" style="left:357px;top:194px;width:70px">Ut wisi enim ad minim veniam, quis nostrud exerci tation ullamcorper</p>
  <div class="side">www.vorlanta.com</div><div class="pg">02</div>
</section>

<!-- Features laptop -->
<section class="slide glow c1" style="top:1228px">
  <div class="brand"><span class="dot"></span>Vorlanta</div>
  <span class="tag" style="left:42px;top:30px">Product</span>
  <div class="title" style="left:42px;top:40px">Features</div>
  <div class="abs" style="left:42px;top:84px;width:174px;height:117px;background:#1b1b1b;border-radius:5px;padding:5px"><div style="width:100%;height:100%;background:#fff"></div></div>
  <div class="abs" style="left:20px;top:201px;width:218px;height:5px;background:#9b9b9b;border-radius:0 0 6px 6px"></div>
  <div class="abs label" style="left:258px;top:66px">Ut wisi enim ad minim veniam</div>
  <ul class="body" style="left:264px;top:80px;width:170px;list-style:disc;padding-left:6px">
    <li>lorem ipsum dolor sit amet, consectetuer adipiscing elit, sed diam</li>
    <li>nonummy nibh euismod tincidunt ut laoreet dolore magna aliquam erat volutpat.</li>
    <li>ut wisi enim ad minim veniam, quis nostrud exerci tation ullamcorper suscipit</li>
    <li>lobortis nisl ut aliquip ex ea commodo consequat.</li>
  </ul>
  <div class="ico" style="left:258px;top:153px;width:26px;height:26px"><svg viewBox="0 0 12 12"><path d="M3 9l6-6M5 3h4v4"/></svg></div>
  <p class="body" style="left:258px;top:187px;width:70px">Ut wisi enim ad minim veniam, quis nostrud exerci tation ullamcorper</p>
  <div class="ico y" style="left:352px;top:153px;width:26px;height:26px"><svg viewBox="0 0 12 12"><circle cx="6" cy="5" r="3"/><path d="M5 10h2"/></svg></div>
  <p class="body" style="left:352px;top:187px;width:70px">Ut wisi enim ad minim veniam, quis nostrud exerci tation ullamcorper</p>
  <div class="side">www.vorlanta.com</div><div class="pg">02</div>
</section>

<!-- Features phone -->
<section class="slide glow c2" style="top:1228px">
  <div class="brand"><span class="dot"></span>Vorlanta</div>
  <span class="tag" style="left:36px;top:30px">Product</span>
  <div class="title" style="left:36px;top:40px">Features</div>
  <div class="abs" style="left:190px;top:54px;width:88px;height:178px;border:3px solid #222;outline:1px solid #888;border-radius:14px;background:#fff"><div style="width:24px;height:5px;background:#111;border-radius:3px;margin:5px auto"></div></div>
  <p class="body" style="left:35px;top:90px;width:108px;text-align:right">Ut wisi enim ad minim veniam, quis nostrud exerci tation ullamcorper</p>
  <p class="body" style="left:35px;top:132px;width:108px;text-align:right">Ut wisi enim ad minim veniam, quis nostrud exerci tation ullamcorper</p>
  <p class="body" style="left:35px;top:174px;width:108px;text-align:right">Ut wisi enim ad minim veniam, quis nostrud exerci tation ullamcorper</p>
  <div class="ico" style="left:150px;top:90px;width:24px;height:24px"><svg viewBox="0 0 12 12"><path d="M3 9l6-6M5 3h4v4"/></svg></div>
  <div class="ico y" style="left:150px;top:132px;width:24px;height:24px"><svg viewBox="0 0 12 12"><circle cx="6" cy="5" r="3"/><path d="M5 10h2"/></svg></div>
  <div class="ico" style="left:150px;top:174px;width:24px;height:24px"><svg viewBox="0 0 12 12"><path d="M3 9l6-6M5 3h4v4"/></svg></div>
  <div class="ico" style="left:294px;top:90px;width:24px;height:24px"><svg viewBox="0 0 12 12"><path d="M3 9l6-6M5 3h4v4"/></svg></div>
  <div class="ico y" style="left:294px;top:132px;width:24px;height:24px"><svg viewBox="0 0 12 12"><circle cx="6" cy="5" r="3"/><path d="M5 10h2"/></svg></div>
  <div class="ico" style="left:294px;top:174px;width:24px;height:24px"><svg viewBox="0 0 12 12"><path d="M3 9l6-6M5 3h4v4"/></svg></div>
  <p class="body" style="left:326px;top:90px;width:108px">Ut wisi enim ad minim veniam, quis nostrud exerci tation ullamcorper</p>
  <p class="body" style="left:326px;top:132px;width:108px">Ut wisi enim ad minim veniam, quis nostrud exerci tation ullamcorper</p>
  <p class="body" style="left:326px;top:174px;width:108px">Ut wisi enim ad minim veniam, quis nostrud exerci tation ullamcorper</p>
  <div class="side">www.vorlanta.com</div><div class="pg">02</div>
</section>

<!-- Chart & Statistics -->
<section class="slide glow c1" style="top:1523px">
  <div class="brand"><span class="dot"></span>Vorlanta</div>
  <span class="tag" style="left:33px;top:34px">Product</span>
  <div class="title" style="left:33px;top:44px">Chart &amp; Statistics</div>
  <div class="abs" style="left:33px;top:82px;width:406px;height:126px;background:var(--panel)"></div>
  <div class="abs" style="left:33px;top:82px;width:115px;height:98px;background:#3d0d0e;padding:7px 9px">
    <div style="font-size:7px;font-weight:600;line-height:1.2">Ut wisi enim ad<br>minim veniam</div>
    <div style="font-size:22px;font-weight:700;color:var(--yellow);margin-top:4px">$8.5M</div>
    <div style="font-size:5.5px;line-height:1.3;color:var(--muted)">Ut wisi enim ad minim veniam, quis nostrud exerci tation ullamcorper</div>
  </div>
  <div class="abs" style="left:33px;top:185px;width:115px;height:23px;background:#3d2a0e;font-size:6px;font-weight:600;display:flex;align-items:center;padding-left:10px"><span style="color:var(--yellow);margin-right:4px">▥</span>Ut wisi enim ad minim</div>
  <svg class="abs" style="left:162px;top:88px" width="270" height="115" viewBox="0 0 270 115">
    <g stroke="#5a2222" stroke-width=".5"><path d="M10 5h255M10 22h255M10 39h255M10 56h255M10 73h255M10 90h255M10 107h255"/></g>
    <g>
      <rect x="24" y="35" width="11" height="72" fill="#c8161d"/><rect x="37" y="71" width="11" height="36" fill="#ee7a22"/><rect x="50" y="71" width="11" height="36" fill="#f6e21f"/>
      <rect x="86" y="63" width="11" height="44" fill="#c8161d"/><rect x="99" y="32" width="11" height="75" fill="#ee7a22"/><rect x="112" y="71" width="11" height="36" fill="#f6e21f"/>
      <rect x="148" y="47" width="11" height="60" fill="#c8161d"/><rect x="161" y="71" width="11" height="36" fill="#ee7a22"/><rect x="174" y="52" width="11" height="55" fill="#f6e21f"/>
      <rect x="210" y="32" width="11" height="75" fill="#c8161d"/><rect x="223" y="56" width="11" height="51" fill="#ee7a22"/><rect x="236" y="20" width="11" height="87" fill="#f6e21f"/>
    </g>
    <g fill="#999" font-size="3.5" font-family="Poppins,sans-serif"><text x="34" y="113">Category 1</text><text x="96" y="113">Category 2</text><text x="158" y="113">Category 3</text><text x="220" y="113">Category 4</text></g>
  </svg>
  <p class="body" style="left:33px;top:220px;width:300px;color:#fff">Ut wisi enim ad minim veniam, quis nostrud exerci tation ullamcorper</p>
  <div class="side">www.vorlanta.com</div><div class="pg">02</div>
</section>

<!-- Funnel -->
<section class="slide glow c2" style="top:1523px">
  <div class="brand"><span class="dot"></span>Vorlanta</div>
  <span class="tag" style="left:218px;top:22px">Business</span>
  <div class="title" style="left:198px;top:30px">Funnel</div>
  <div class="funnel-bar" style="left:130px;top:66px;width:210px;height:36px;background:var(--red)">Ut wisi enim ad minim veniam</div>
  <div class="funnel-bar" style="left:148px;top:112px;width:174px;height:36px;background:#d42a1e">Ut wisi enim ad minim veniam</div>
  <div class="funnel-bar" style="left:176px;top:158px;width:118px;height:36px;background:var(--orange)">Ut wisi enim ad minim<br>veniam</div>
  <div class="funnel-bar" style="left:198px;top:204px;width:74px;height:36px;background:var(--yellow)">Ut wisi enim ad<br>minim veniam</div>
  <div class="num" style="left:28px;top:64px;font-size:26px">01</div>
  <div class="body" style="left:28px;top:96px;width:100px"><span class="label">Lorem ipsum dolor</span><br>Ut wisi enim ad minim veniam, quis nostrud exerci tation ullamcorper</div>
  <div class="num" style="left:350px;top:88px;font-size:26px">02</div>
  <div class="body" style="left:350px;top:120px;width:100px"><span class="label">Lorem ipsum dolor</span><br>Ut wisi enim ad minim veniam, quis nostrud exerci tation ullamcorper</div>
  <div class="num" style="left:78px;top:156px;font-size:26px">03</div>
  <div class="body" style="left:78px;top:188px;width:100px"><span class="label">Lorem ipsum dolor</span><br>Ut wisi enim ad minim veniam, quis nostrud exerci tation ullamcorper</div>
  <div class="num" style="left:322px;top:176px;font-size:26px">04</div>
  <div class="body" style="left:322px;top:208px;width:100px"><span class="label">Lorem ipsum dolor</span><br>Ut wisi enim ad minim veniam, quis nostrud exerci tation ullamcorper</div>
  <div class="side">www.vorlanta.com</div><div class="pg">02</div>
</section>

<!-- Best Team -->
<section class="slide glow c1" style="top:1820px">
  <div class="brand"><span class="dot"></span>Vorlanta</div>
  <span class="tag" style="left:34px;top:36px">Business</span>
  <div class="title" style="left:34px;top:46px">Best Team</div>
  <div class="photo" role="img" aria-label="Team member portrait" style="left:52px;top:84px;width:74px;height:74px;background:radial-gradient(circle at 50% 40%,#b88a6a,#5a3a2e 70%)"></div>
  <div class="photo" role="img" aria-label="Team member portrait" style="left:185px;top:84px;width:92px;height:92px;background:radial-gradient(circle at 50% 40%,#c7a487,#6a7a8a 75%)"></div>
  <div class="photo" role="img" aria-label="Team member portrait" style="left:333px;top:84px;width:74px;height:74px;background:radial-gradient(circle at 50% 40%,#bfa08a,#dcdcdc 75%)"></div>
  <div class="body" style="left:40px;top:168px;width:100px;text-align:center"><span class="label">Lorem ipsum dolor</span><br>Ut wisi enim ad minim veniam, quis nostrud exerci tation ullamcorper</div>
  <div class="body" style="left:181px;top:190px;width:100px;text-align:center"><span class="label">Lorem ipsum dolor</span><br>Ut wisi enim ad minim veniam, quis nostrud exerci tation ullamcorper</div>
  <div class="body" style="left:320px;top:168px;width:100px;text-align:center"><span class="label">Lorem ipsum dolor</span><br>Ut wisi enim ad minim veniam, quis nostrud exerci tation ullamcorper</div>
  <div class="side">www.vorlanta.com</div><div class="pg">02</div>
</section>

<!-- Take a break -->
<section class="slide c2" style="top:1820px;background:#3a0808">
  <div class="abs" role="img" aria-label="Concentric red dotted pattern" style="inset:0;background:radial-gradient(circle at 48% 58%,#1a0303 10%,#8c1a1a 28%,#3a0808 45%,#6a1010 60%,#2a0505 80%)"></div>
  <svg class="abs" style="left:228px;top:76px" width="22" height="22" viewBox="0 0 22 22" fill="none" stroke="#f6a81f" stroke-width="1.4" stroke-linecap="round"><path d="M4 4h14l-7 8zM11 12v7M7 19h8M15 2l3 3"/></svg>
  <div class="abs" style="left:0;width:481px;top:104px;text-align:center;font-weight:800;font-size:34px;line-height:1.02;letter-spacing:.5px">TAKE A<br>BREAK</div>
</section>

<!-- Section title -->
<section class="slide glow c1" style="top:2130px">
  <div class="brand" style="top:22px;font-size:18px;gap:5px"><span class="dot" style="width:18px;height:18px"></span>Vorlanta</div>
  <div class="abs" style="left:0;top:84px;width:258px;height:96px;border-radius:0 48px 48px 0;background:linear-gradient(90deg,var(--yellow),var(--orange) 55%,var(--red))"></div>
  <div class="photo" role="img" aria-label="Glowing AI chip held by a robot hand" style="left:168px;top:92px;width:82px;height:82px;background:radial-gradient(circle,#c25cf0,#3a2a8a 70%)"></div>
  <div class="abs" style="left:32px;top:112px;font-weight:800;font-size:18px;line-height:1.2;color:#1a0a05">SECTION<br>TITLE</div>
  <div class="body" style="left:280px;top:110px;width:140px;font-size:10px;color:#fff"><span class="label" style="font-size:10px">Lorem ipsum dolor</span><br>Ut wisi enim ad minim veniam, quis nostrud exerci tation ullamcorper</div>
  <div class="side">www.vorlanta.com</div><div class="pg">02</div>
</section>

<!-- Thank you -->
<section class="slide glow c2" style="top:2130px">
  <div class="abs" style="left:0;width:481px;top:42px;text-align:center;font-weight:600;font-size:76px;line-height:1;color:transparent;-webkit-text-stroke:1.5px #6a1414;white-space:nowrap">Thank You!</div>
  <div class="abs" style="left:0;width:481px;top:50px;text-align:center;font-weight:800;font-size:32px;color:var(--yellow)">Thank You!</div>
  <div class="abs" style="left:0;width:481px;top:164px;display:flex;justify-content:center;align-items:center;gap:8px;font-weight:700;font-size:32px"><span style="width:36px;height:36px;border-radius:50%;background:var(--red)"></span>Vorlanta</div>
  <div class="side">www.vorlanta.com</div><div class="pg">02</div>
</section>

</body>
</html>
```